Homemaking training schools needs a Business Card design

Designer, Hello!

No special requirements, good-looking enough.
--------------------------------------------------------------------------

Name: Marcus Dole
Chairman
Tel: 0574-71948263
Mobile: 13857420916
Email: kelvora@mailnest.example
Web: www.prt2019.example
Add: No.258, LanpingJie, BeiyuanQu, Ningbo, Zhejiang

LOGO
Ningbo PRT Homemaking Training School

Target Market(s)

pregnant women, mothers, infants, the elderly and families, including cleaning, cooking, nursing training.

Industry/Entity Type

Business

Contact Information for Business Card

Name: Marcus Dole
Chairman
Tel: 0574-71948263
Mobile: 13857420916
Email: kelvora@mailnest.example
Web: www.prt2019.example

LOGO

Font styles to use
Serif
Sans Serif
Decorative

Requirements
Nice to have
• Feels: clean, specifications, safety, comfort, warmth and happiness.

```html
<!DOCTYPE html>
<html lang="en">
<head>
<meta charset="utf-8">
<title>Pei RunTang Business Card</title>
<link rel="stylesheet" href="https://fonts.googleapis.com/css2?family=Montserrat:ital,wght@0,400;0,600;0,800;1,400&display=swap">
<style>
  :root {
    --brand-blue: #2f6dc1;
    --brand-pink: #e8348b;
    --ink: #1c1c1c;
    --paper: #ffffff;
    --backdrop: #e9e7e3;
  }
  * { box-sizing: border-box; margin: 0; padding: 0; }
  html, body { width: 1200px; height: 1200px; overflow: hidden; }
  body {
    background: var(--backdrop);
    display: flex;
    flex-direction: column;
    align-items: center;
    justify-content: center;
    gap: 70px;
    font-family: "Montserrat", sans-serif;
  }
  .card {
    position: relative;
    width: 860px;
    height: 490px;
    background: var(--paper);
    box-shadow: 0 6px 22px rgba(0,0,0,0.12);
  }

  /* Name side */
  .card--brand {
    display: flex;
    flex-direction: column;
    align-items: center;
    justify-content: center;
  }
  .brand-name {
    font-family: "Montserrat", sans-serif;
    font-weight: 600;
    font-size: 58px;
    color: var(--brand-blue);
  }
  .school-name {
    margin-top: 40px;
    font-size: 21px;
    font-weight: 400;
    color: var(--ink);
    letter-spacing: 0.3px;
  }

  /* Contact side */
  .accent {
    position: absolute;
    height: 4px;
    width: 160px;
    background: linear-gradient(to right, var(--brand-pink) 50%, var(--brand-blue) 50%);
  }
  .accent--top { top: 62px; right: 70px; width: 100px; }
  .accent--bottom { left: 70px; bottom: 70px; }
  .contact {
    position: absolute;
    right: 70px;
    top: 86px;
    text-align: right;
  }
  .contact__name {
    font-weight: 800;
    font-size: 40px;
    color: var(--brand-blue);
    text-transform: uppercase;
    letter-spacing: -0.5px;
  }
  .contact__role {
    font-style: italic;
    font-size: 14px;
    color: var(--brand-blue);
    text-transform: uppercase;
    margin-top: 2px;
  }
  .contact__address {
    margin-top: 36px;
    font-weight: 600;
    font-size: 21px;
    line-height: 1.45;
    color: var(--ink);
  }
  .contact__lines {
    margin-top: 26px;
    font-size: 27px;
    line-height: 1.5;
    color: var(--brand-blue);
  }
</style>
</head>
<body>
  <section class="card card--brand">
    <p class="brand-name">Pei RunTang</p>
    <p class="school-name">Ningbo PRT Homemaking Training School</p>
  </section>

  <section class="card card--contact">
    <span class="accent accent--top"></span>
    <div class="contact">
      <h1 class="contact__name">Marcus Dole</h1>
      <p class="contact__role">Chairman</p>
      <p class="contact__address">No.258, LanpingJie, BeiyuanQu<br>Ningbo, Zhejiang</p>
      <p class="contact__lines">0574-71948263 | 13857420916<br>kelvora@mailnest.example | www.prt2019.example</p>
    </div>
    <span class="accent accent--bottom"></span>
  </section>
</body>
</html>
```